Business Card Design - VNT (company name)

Over 20 years of progressive technology design, migration and management experience that drives business objectives and streamlines operations. Continuously challenge conventions to meet and exceed business security, availability and functionality requirements. Maintain exceptional vendor relationships to ensure ongoing knowledge of emerging products and to secure preferred service agreements. Recruit and utilize top talent and foster a collegial environment that advances innovation and performance excellence. design logo using 3 arrows of different colors green, gold, blue

Industry/Entity Type

Progressive

Contact Information for Business Card

Martin K. Osgood
IT Strategist / Consultant

626.583.2907 MOsgood@vntosgood.example 4817 Brenning Court Pasadena, CA 91104

Colors
0255a3
f37122
fece3e

Requirements
Must have
• Note NEW EMAIL ADDRESS
• MOsgood@vntosgood.example
• NOTE NEW ORDER of the work I do.
• Infrastructure – Systems – Cybersecurity
Nice to have
• main color should be orange

```html
<!DOCTYPE html>
<html lang="en">
<head>
<meta charset="utf-8">
<title>VNT Business Card</title>
<link rel="stylesheet" href="https://fonts.googleapis.com/css2?family=Lato:wght@400;700&family=Arimo:wght@400&display=swap">
<style>
  :root {
    --backdrop: #1f2426;
    --card-light: #eef0ef;
    --card-light-edge: #e2e5e4;
    --brand-orange: #f06818;
    --brand-blue: #0255a3;
    --ink: #2f3336;
    --white: #ffffff;
  }
  html, body {
    margin: 0;
    padding: 0;
    width: 1200px;
    height: 864px;
    overflow: hidden;
    background: var(--backdrop);
  }
  .canvas {
    position: relative;
    width: 1200px;
    height: 864px;
  }
  .card {
    position: absolute;
    box-sizing: border-box;
  }
  .card-front {
    left: 320px;
    top: 80px;
    width: 561px;
    height: 330px;
    background: linear-gradient(135deg, var(--card-light) 0%, var(--card-light-edge) 100%);
  }
  .card-back {
    left: 318px;
    top: 452px;
    width: 563px;
    height: 333px;
    background: var(--brand-orange);
  }
  .holder-name {
    position: absolute;
    left: 50px;
    top: 54px;
    margin: 0;
    font-family: "Lato", sans-serif;
    font-weight: 700;
    font-size: 25px;
    line-height: 1;
    color: var(--brand-orange);
  }
  .holder-title {
    position: absolute;
    left: 50px;
    top: 83px;
    margin: 0;
    font-family: "Lato", sans-serif;
    font-weight: 400;
    font-size: 17px;
    line-height: 1;
    color: var(--ink);
  }
  .contact-list {
    position: absolute;
    left: 49px;
    top: 175px;
    margin: 0;
    font-family: "Arimo", sans-serif;
    font-size: 15px;
    line-height: 19.5px;
  }
  .contact-list dt {
    color: var(--brand-orange);
  }
  .contact-list dd {
    margin: 0;
    color: var(--ink);
  }
  .wordmark {
    position: absolute;
    font-family: "Lato", sans-serif;
    font-weight: 700;
    line-height: 1;
    letter-spacing: 2px;
  }
  .card-front .wordmark {
    left: 282px;
    top: 122px;
    width: 250px;
    text-align: center;
    font-size: 84px;
    color: var(--brand-blue);
  }
  .card-back .wordmark {
    left: 0;
    top: 92px;
    width: 100%;
    text-align: center;
    font-size: 112px;
    color: var(--white);
  }
  .services {
    position: absolute;
    left: 0;
    top: 252px;
    width: 100%;
    margin: 0;
    text-align: center;
    font-family: "Lato", sans-serif;
    font-size: 17px;
    color: var(--white);
  }
</style>
</head>
<body>
<main class="canvas">
  <section class="card card-front" aria-label="Business card front">
    <h1 class="holder-name">Martin K. Osgood</h1>
    <p class="holder-title">IT Strategist / Consultant</p>
    <dl class="contact-list">
      <dt>telephone</dt>
      <dd>626.583.2907</dd>
      <dt>email</dt>
      <dd>MOsgood@vntosgood.example</dd>
      <dt>address</dt>
      <dd>4817 Brenning Court</dd>
    </dl>
    <div class="wordmark">VNT</div>
  </section>

  <section class="card card-back" aria-label="Business card back">
    <div class="wordmark">VNT</div>
    <p class="services">Infrastructure &nbsp;|&nbsp; Systems &nbsp;|&nbsp; Cybersecurity</p>
  </section>
</main>
</body>
</html>
```